Business cards to launch an education platform

Hi,
I am looking at having new business cards designed.
I am a startup, developing a web platform for schools and university, the education world. It's an online assessment system.
I would like a card that looks classy, and that is using the colors and the font of my logo.

I have attached:
1) my logo
2) A business card that I have designed quickly so you can have all the information required in the card, but I really don't like it.
3) The font that I am using (Lato Regular) to design my web platform
4) Some screenshots of my web platform so you can have a look at the style that I have.

Target Market(s)

Major market: Education system: Schools and university
Minor markets: Business in general

Industry/Entity Type

Business

Contact Information for Business Card

Clara Fenwick
Director

M: 0437 518 902
E: clara.fenwick@amberLoomSystems.com.au

Requirements
Must have
• The colors of my logo

```html
<!DOCTYPE html>
<html lang="en">
<head>
<meta charset="utf-8">
<title>Amber Loom Systems – Business Card</title>
<link rel="stylesheet" href="https://fonts.googleapis.com/css2?family=Lato:wght@400&family=Oswald:wght@400;500&family=Roboto+Condensed:wght@400&display=swap">
<style>
  :root {
    --backdrop: #9a9b9c;
    --card-light: #e4e5e7;
    --card-navy: #053667;
    --ink-navy: #0f3d6e;
    --ink-grey: #474a4f;
    --brand-blue: #1f6fb8;
    --white: #ffffff;
  }
  * { margin: 0; padding: 0; box-sizing: border-box; }
  html, body {
    width: 1105px;
    height: 1200px;
    overflow: hidden;
    background: var(--backdrop);
  }
  .canvas {
    position: relative;
    width: 1105px;
    height: 1200px;
  }
  .card {
    position: absolute;
    left: 182px;
    width: 746px;
    height: 426px;
    overflow: hidden;
  }
  .card--front { top: 120px; background: var(--card-light); }
  .card--back  { top: 637px; background: var(--card-navy); }

  /* Front: brand block */
  .brand {
    position: absolute;
    left: 64px;
    top: 128px;
    width: 260px;
    text-align: center;
  }
  .brand__square {
    display: block;
    width: 58px;
    height: 58px;
    margin: 0 auto 22px;
    background: var(--brand-blue);
  }
  .brand__name {
    font-family: "Lato", sans-serif;
    font-weight: 400;
    font-size: 29px;
    line-height: 1.2;
    letter-spacing: 2px;
    color: var(--ink-navy);
  }

  /* Front: person and contact */
  .person {
    position: absolute;
    left: 349px;
    top: 118px;
  }
  .person__name {
    font-family: "Oswald", sans-serif;
    font-weight: 500;
    font-size: 34px;
    line-height: 1.1;
    color: var(--ink-navy);
  }
  .person__role {
    font-family: "Oswald", sans-serif;
    font-weight: 400;
    font-size: 25px;
    line-height: 1.3;
    color: var(--ink-grey);
  }
  .contact {
    position: absolute;
    left: 351px;
    top: 214px;
    list-style: none;
  }
  .contact__item {
    display: flex;
    align-items: center;
    height: 29px;
    font-family: "Roboto Condensed", sans-serif;
    font-size: 18px;
    color: var(--ink-grey);
  }
  .contact__icon {
    width: 16px;
    height: 16px;
    margin-right: 14px;
    fill: var(--ink-navy);
    flex: none;
  }

  /* Back */
  .back-brand {
    position: absolute;
    left: 55px;
    top: 278px;
    color: var(--white);
    font-family: "Lato", sans-serif;
    font-weight: 400;
  }
  .back-brand__name {
    font-size: 40px;
    line-height: 1.15;
    letter-spacing: 3px;
  }
  .back-brand__web {
    font-size: 20px;
    margin-top: 6px;
  }
</style>
</head>
<body>
<main class="canvas">

  <section class="card card--front" aria-label="Business card front">
    <div class="brand">
      <span class="brand__square"></span>
      <p class="brand__name">AMBER LOOM<br>SYSTEMS</p>
    </div>

    <div class="person">
      <h1 class="person__name">Clara Fenwick</h1>
      <p class="person__role">Director</p>
    </div>

    <ul class="contact">
      <li class="contact__item">
        <svg class="contact__icon" viewBox="0 0 16 16" aria-hidden="true">
          <path d="M4 0h8a1.5 1.5 0 0 1 1.5 1.5v13A1.5 1.5 0 0 1 12 16H4a1.5 1.5 0 0 1-1.5-1.5v-13A1.5 1.5 0 0 1 4 0zm0 2v10.5h8V2H4zm4 11.2a.9.9 0 1 0 0 1.8.9.9 0 0 0 0-1.8z"/>
        </svg>
        0437 518 902
      </li>
      <li class="contact__item">
        <svg class="contact__icon" viewBox="0 0 16 16" aria-hidden="true">
          <path d="M0 3h16v1.2L8 9 0 4.2V3zm0 2.6 8 4.8 8-4.8V13H0V5.6z"/>
        </svg>
        clara.fenwick@amberLoomSystems.com.au
      </li>
      <li class="contact__item">
        <svg class="contact__icon" viewBox="0 0 16 16" aria-hidden="true">
          <circle cx="8" cy="8" r="7.5"/>
          <path d="M4 5c1.5-.5 2.5.5 2 2s1 2 1 3.5S5.5 12 5 10 3 8 4 5zm5-2c1.5 0 3 1 3.5 2.5-1 .5-2 0-2.5 1s1 2 0 3.5S8.5 8 8.5 6.5 8 3.5 9 3z" fill="var(--card-light)"/>
        </svg>
        www.amberLoomSystems.com.au
      </li>
    </ul>
  </section>

  <section class="card card--back" aria-label="Business card back">
    <div class="back-brand">
      <p class="back-brand__name">AMBER LOOM<br>SYSTEMS</p>
      <p class="back-brand__web">amberLoomSystems.com.au</p>
    </div>
  </section>

</main>
</body>
</html>
```